Business card design needed

I would like a one sided black business card with the information provided above. Refer to my website www.brightvolleyracquets.com.au for an example of colors I have used for my site, would like to keep this consistent for my business cards also, I will upload my logo below.

I am a new small business that provides tennis customers with racquet re stringing, tennis strings and accessories.

Industry/Entity Type

Small Business

Contact Information for Business Card

Bright Volley Tennis

Owen Whitby
Managing Director

brightvolleyracquets@mailbox.example
www.brightvolleyracquets.com.au
0491 726 305

Racquet Restringing/Tennis Strings/Accessories

Requirements
Must have
• Must have my logo and card must be black

```html
<!DOCTYPE html>
<html lang="en">
<head>
<meta charset="utf-8">
<title>Bright Volley Tennis – Business Card</title>
<link rel="stylesheet" href="https://fonts.googleapis.com/css2?family=Open+Sans:ital,wght@0,400;0,700;1,700&display=swap">
<style>
  :root {
    --backdrop: #d9d6d2;
    --card: #000000;
    --lime: #b3d334;
    --white: #ffffff;
  }
  * { margin: 0; padding: 0; box-sizing: border-box; }
  html, body {
    width: 1200px;
    height: 750px;
    overflow: hidden;
    background: var(--backdrop);
    font-family: "Open Sans", sans-serif;
  }
  .card {
    position: absolute;
    left: 75px;
    top: 75px;
    width: 1050px;
    height: 600px;
    background: var(--card);
    border-radius: 40px;
    color: var(--white);
    text-align: center;
  }
  .brand {
    position: absolute;
    top: 150px;
    left: 0;
    right: 0;
    display: flex;
    justify-content: center;
    align-items: center;
    gap: 22px;
  }
  .brand-dot {
    width: 46px;
    height: 46px;
    border-radius: 50%;
    background: var(--lime);
  }
  .brand-name {
    font-weight: 700;
    font-size: 54px;
    color: var(--lime);
    letter-spacing: 1px;
  }
  .services {
    position: absolute;
    top: 335px;
    left: 0;
    right: 0;
    font-size: 33px;
    display: flex;
    justify-content: center;
    gap: 22px;
  }
  .services li { list-style: none; display: flex; align-items: center; }
  .services li::before {
    content: "";
    width: 10px;
    height: 10px;
    background: var(--white);
    margin-right: 12px;
  }
  .person {
    position: absolute;
    top: 420px;
    left: 0;
    right: 0;
    font-size: 24px;
  }
  .person-name { color: var(--lime); font-weight: 700; font-size: 31px; }
  .contact {
    position: absolute;
    left: 0;
    right: 0;
    font-size: 24px;
  }
  .contact-phone { top: 482px; }
  .contact-online { top: 537px; }
  .label { font-weight: 700; font-style: italic; }
  .divider { margin: 0 12px 0 20px; }
</style>
</head>
<body>
  <div class="card">
    <div class="brand">
      <span class="brand-dot"></span>
      <span class="brand-name">Bright Volley Tennis</span>
    </div>

    <ul class="services">
      <li>Racquet Restringing</li>
      <li>Tennis Strings</li>
      <li>Accessories</li>
    </ul>

    <p class="person"><span class="person-name">Owen Whitby -</span> Managing Director</p>

    <p class="contact contact-phone"><span class="label">phone</span> 0491 726 305</p>

    <p class="contact contact-online">
      <span class="label">email</span> brightvolleyracquets@mailbox.example<span class="divider">|</span><span class="label">web</span> www.brightvolleyracquets.com.au
    </p>
  </div>
</body>
</html>
```